Full re-design of visual identity

We have just re-designed our logo and would like to apply it on our folders, business cards, stationery, and etc... we are attaching new logo + the material we need to re-design... we will provide full corel draw files to help make job easier and also because lot of icons and artwork can be still used...

any doubts we are at your disposal. thanks in advance.

```html
<!DOCTYPE html>
<html lang="en">
<head>
<meta charset="utf-8">
<title>Nordwave business card</title>
<link rel="stylesheet" href="https://fonts.googleapis.com/css2?family=Arimo:wght@400;700&display=swap">
<style>
  :root {
    --orange: #ef8a22;
    --orange-deep: #d9651f;
    --gray: #7a7a7a;
    --gray-light: #a9a9a9;
    --ink: #333333;
    --paper: #ffffff;
    --backdrop: #ecebe8;
  }
  * { margin: 0; padding: 0; box-sizing: border-box; }
  html, body { width: 1200px; height: 900px; overflow: hidden; }
  body {
    background: var(--backdrop);
    font-family: "Arimo", Arial, sans-serif;
    display: flex; flex-direction: column; align-items: center; justify-content: center;
    gap: 50px;
  }
  .card {
    width: 640px; height: 366px; position: relative; overflow: hidden;
    box-shadow: 0 6px 18px rgba(0,0,0,.18);
  }
  /* front */
  .card-front { background: var(--paper); }
  .brand {
    position: absolute; left: 36px; top: 120px; width: 314px;
    display: flex; flex-direction: column; align-items: center;
  }
  .brand-row { display: flex; align-items: center; gap: 12px; }
  .brand-dot { width: 34px; height: 34px; border-radius: 50%; background: var(--orange); }
  .brand-name { font-size: 56px; font-weight: 700; color: var(--gray); letter-spacing: -1px; line-height: 1; }
  .brand-tagline { margin-top: 8px; font-size: 12px; color: var(--orange); letter-spacing: .5px; }
  .divider {
    position: absolute; left: 370px; top: 26px; height: 250px; width: 2px;
    background: linear-gradient(to bottom, rgba(0,0,0,0), rgba(0,0,0,.18) 30%, rgba(0,0,0,.18) 70%, rgba(0,0,0,0));
  }
  .contact { position: absolute; left: 392px; top: 28px; color: var(--ink); }
  .contact-name { font-size: 20px; color: var(--orange); }
  .contact-role { font-size: 14px; margin-top: 2px; }
  .contact-list { margin-top: 34px; font-size: 12px; line-height: 1.2; }
  .contact-label { text-transform: uppercase; margin-top: 6px; }
  .contact-value { color: var(--gray); }
  .footer-band { position: absolute; left: 0; right: 0; bottom: 0; height: 30px; display: flex; }
  .footer-band-accent { flex: 1; background: linear-gradient(to right, var(--orange-deep), var(--orange)); }
  .footer-band-web {
    width: 250px; background: var(--gray-light); color: var(--paper);
    font-size: 14px; display: flex; align-items: center; justify-content: flex-end; padding-right: 28px; gap: 10px;
  }
  .footer-band-web::before { content: ""; width: 12px; height: 12px; border-radius: 50%; background: var(--paper); }
  /* back */
  .card-back {
    background: linear-gradient(160deg, var(--orange) 0%, var(--orange-deep) 100%);
    display: flex; align-items: center; justify-content: center; gap: 18px;
  }
  .card-back .brand-dot { width: 60px; height: 60px; background: var(--paper); }
  .card-back .brand-name { color: var(--paper); font-size: 84px; }
</style>
</head>
<body>
  <section class="card card-front">
    <div class="brand">
      <div class="brand-row">
        <span class="brand-dot"></span>
        <span class="brand-name">nordwave</span>
      </div>
      <span class="brand-tagline">network · cloud · fiber</span>
    </div>
    <div class="divider"></div>
    <div class="contact">
      <p class="contact-name">Daniel Reyes</p>
      <p class="contact-role">President</p>
      <div class="contact-list">
        <p class="contact-label">Address:</p>
        <p class="contact-value">48 Harbor Lane, VA, 22140</p>
        <p class="contact-label">Phone:</p>
        <p class="contact-value">555 210 4410</p>
        <p class="contact-label">Fax:</p>
        <p class="contact-value">555 210 4411</p>
        <p class="contact-label">Email:</p>
        <p class="contact-value">hello@nordwave.net</p>
      </div>
    </div>
    <div class="footer-band">
      <div class="footer-band-accent"></div>
      <div class="footer-band-web">www.nordwave.net</div>
    </div>
  </section>

  <section class="card card-back">
    <span class="brand-dot"></span>
    <span class="brand-name">nordwave</span>
  </section>
</body>
</html>
```